Moravel Aesthetic Doctor

I require an elegant, luxurious looking business card for my aesthetic business. I am a doctor and that will set me aside from competitors. I am planning to provide home and spa based treatments to clients with high expectations. I have attached my logo.

```html
<!DOCTYPE html>
<html lang="en">
<head>
<meta charset="utf-8">
<title>Moravel Aesthetic Doctor — Business Card</title>
<link href="https://fonts.googleapis.com/css2?family=Montserrat:wght@400;500&display=swap" rel="stylesheet">
<style>
  :root {
    --backdrop: #2b2b2d;
    --card: #fbfbfc;
    --card-back: #f1f1f2;
    --ink: #2a2a2e;
    --grey: #8c8d92;
    --blue: #2f8fd4;
    --blue-soft: #6cb6e6;
  }
  * { margin: 0; padding: 0; box-sizing: border-box; }
  html, body { width: 1200px; height: 900px; overflow: hidden; }
  body {
    background: var(--backdrop);
    font-family: "Montserrat", sans-serif;
    color: var(--ink);
    position: relative;
  }
  .card {
    position: absolute;
    top: 140px;
    width: 340px;
    height: 610px;
    border-radius: 26px;
    display: flex;
    flex-direction: column;
    align-items: center;
    text-align: center;
  }
  .card--front { left: 225px; background: var(--card); padding-top: 56px; }
  .card--back { left: 635px; background: var(--card-back); padding-top: 150px; }

  .brand { display: flex; flex-direction: column; align-items: center; gap: 16px; }
  .brand__mark {
    width: 92px; height: 92px; border-radius: 50%;
    background: linear-gradient(135deg, var(--blue-soft), var(--blue));
  }
  .brand__name {
    font-weight: 500; font-size: 23px; line-height: 1.25;
    letter-spacing: 2px; text-transform: uppercase; color: var(--blue);
  }
  .tagline { margin-top: 14px; font-size: 14px; color: var(--grey); }

  .doctor { margin-top: 30px; font-size: 14px; line-height: 1.5; }
  .doctor__name { font-weight: 500; }
  .doctor__cred { font-size: 12.5px; }
  .divider { width: 16px; height: 3px; background: var(--blue); margin: 14px 0; }
  .services { list-style: none; font-size: 13px; line-height: 1.55; }

  .icons { display: flex; gap: 22px; margin-top: 26px; }
  .icon {
    width: 28px; height: 28px; border-radius: 50%; background: var(--blue);
    display: flex; align-items: center; justify-content: center;
  }
  .contact { margin-top: 22px; font-size: 15px; line-height: 1.95; }
  .contact .accent { color: var(--blue); }
  .social { display: flex; gap: 12px; margin-top: 10px; }
  .social span { width: 22px; height: 22px; border-radius: 50%; background: var(--blue); }
</style>
</head>
<body>
  <section class="card card--front">
    <div class="brand">
      <div class="brand__mark" role="img" aria-label="Brand emblem area"></div>
      <div class="brand__name">Moravel<br>Aesthetic Doctor</div>
    </div>
    <div class="doctor">
      <p class="doctor__name">Dr.Elise Varnholt MRCPCH MD</p>
      <p class="doctor__cred">Australasian Diploma of Aesthetic Medicine</p>
    </div>
    <div class="divider"></div>
    <ul class="services">
      <li>Dermal injectables | Plasma facials</li>
      <li>Microneedling | Skin boosters</li>
      <li>Excessive sweating</li>
      <li>Home and Spa Based Treatments</li>
    </ul>
    <div class="icons">
      <span class="icon" aria-label="Phone">
        <svg width="14" height="14" viewBox="0 0 24 24"><path fill="#fff" d="M6.6 10.8a15 15 0 0 0 6.6 6.6l2.2-2.2c.3-.3.7-.4 1-.2 1.1.4 2.3.6 3.6.6.6 0 1 .4 1 1V20c0 .6-.4 1-1 1A17 17 0 0 1 3 4c0-.6.4-1 1-1h3.5c.6 0 1 .4 1 1 0 1.3.2 2.5.6 3.6.1.3 0 .7-.2 1z"/></svg>
      </span>
      <span class="icon" aria-label="Email">
        <svg width="14" height="12" viewBox="0 0 24 18"><rect x="1" y="1" width="22" height="16" rx="2" fill="none" stroke="#fff" stroke-width="2"/><path d="M2 2l10 8 10-8" fill="none" stroke="#fff" stroke-width="2"/></svg>
      </span>
      <span class="icon" aria-label="Website">
        <svg width="14" height="14" viewBox="0 0 24 24"><path d="M10 14a5 5 0 0 0 7 0l3-3a5 5 0 0 0-7-7l-1 1M14 10a5 5 0 0 0-7 0l-3 3a5 5 0 0 0 7 7l1-1" fill="none" stroke="#fff" stroke-width="2.4" stroke-linecap="round"/></svg>
      </span>
    </div>
    <div class="contact">
      <p>0800 555 014</p>
      <p>elise@moravel.co.nz</p>
      <p>www.<span class="accent">moravel</span>.co.nz</p>
    </div>
    <div class="social" aria-label="Social profiles"><span></span><span></span></div>
  </section>

  <section class="card card--back">
    <div class="brand">
      <div class="brand__mark" role="img" aria-label="Brand emblem area"></div>
      <div class="brand__name">Moravel<br>Aesthetic Doctor</div>
    </div>
    <p class="tagline">Home and Spa Based Treatments</p>
  </section>
</body>
</html>
```